Professional Single Page Website Design for Tollbrook Advisory

Tollbrook Advisory is a new business consultancy specializing in providing expert services to small businesses, primarily in the brick-and-mortar retail and food service sectors. We offer a range of services including franchise development and launch, due diligence, and construction management.

Currently, we have a basic website set up at www.tollbrookadvisory.example, but we need a professional touch to enhance its design and functionality.

Project Requirements:
- Single Page Design: For now, we need a single page design that effectively showcases who we are, our services, and contact information.
- Future Expansion: The design should be flexible and scalable for future expansion to include additional pages like specific service offerings, about us, and a dedicated contact page.
- Design Aesthetic: We are looking for a modern yet professional design that aligns with our brand identity.
- Logo: We have a logo that we like, which was also sourced from Pixel Bazaar. The logo files are attached to this project brief.

Key Sections to Include:
- Hero Section: An engaging introduction to Tollbrook Advisory with a strong visual impact.
- About Us: A brief overview of who we are and our mission.
- Team: Section for the profiles of the two principals.
- Services: A clear and concise presentation of our services, including franchise development, due diligence, and construction management.
- Contact Information: Easy-to-find contact details, including a form for inquiries.
- Call to Action: Encouraging visitors to get in touch with us for consultations or further information.

Design Considerations:
- Ensure the design is responsive and mobile-friendly.
- Include high-quality images and icons that complement our services and industry.
- We do not need development services, this is only a design project.

```html
<!DOCTYPE html>
<html lang="en">
<head>
<meta charset="utf-8">
<title>Tollbrook Advisory</title>
<link href="https://fonts.googleapis.com/css2?family=Montserrat:wght@400;500;600;700;800&display=swap" rel="stylesheet">
<style>
:root{
  --ink:#26323a;
  --ink-deep:#1f2a31;
  --sage:#94c9b0;
  --mist:#eceeee;
  --paper:#ffffff;
  --text:#2b2f33;
}
*{margin:0;padding:0;box-sizing:border-box}
html,body{width:1200px;height:4206px;overflow:hidden}
body{position:relative;font-family:'Montserrat',sans-serif;color:var(--text);background:var(--paper)}
.abs{position:absolute}
.accent{color:var(--sage)}
.brand{display:flex;align-items:center;gap:12px;font-weight:600;color:var(--ink)}
.brand .dot{border-radius:50%;border:5px solid var(--sage)}
.pin{display:flex;align-items:center;gap:16px;font-size:14px;font-weight:600;color:var(--ink)}
.btn{display:flex;align-items:center;justify-content:center;gap:10px;font-weight:600;border-radius:4px}
.btn-dark{background:var(--ink);color:#fff}
.btn-light{background:#fff;color:var(--ink)}
.nav a{position:absolute;top:120px;font-size:14px;font-weight:500;color:var(--ink);text-decoration:none}
.sep{position:absolute;top:118px;font-size:14px;color:var(--ink)}
.hero-title{left:642px;top:272px;font-size:37px;line-height:71px;font-weight:700;color:#fff;white-space:nowrap;letter-spacing:-0.3px}
.hero-lead{left:642px;top:420px;width:480px;font-size:19px;line-height:45px;font-weight:500;color:#fff}
.section-title{position:absolute;left:0;width:1200px;text-align:center;font-size:33px;font-weight:500;color:var(--ink)}
.card{position:absolute;top:1687px;height:402px;background:#fff;padding:28px 24px}
.card h3{font-size:20px;font-weight:500;line-height:36px;margin-top:16px;color:var(--ink)}
.card p{font-size:15px;line-height:34px;margin-top:12px}
.card .btn{position:absolute;left:24px;top:328px;width:140px;height:46px;font-size:13px}
.card.active{background:linear-gradient(180deg,var(--ink) 0%,#46555e 55%,#eceeee 100%);color:#fff}
.card.active h3{color:#fff}
.member{position:absolute;top:2797px;width:472px;height:347px;border-radius:4px;padding:11px}
.member .photo{width:216px;height:325px;border-radius:3px}
.member .info{position:absolute;left:247px;top:22px;width:210px}
.member p{font-size:15px;line-height:36px}
.member h4{font-size:17px;font-weight:600;margin-top:8px}
.member .role{font-size:17px;font-weight:600;color:var(--sage);margin-top:14px}
.member .icons{display:flex;gap:28px;margin-top:20px}
.field{position:absolute;height:38px;border-bottom:2px solid var(--ink);font-size:15px;font-weight:500;color:var(--ink);display:flex;justify-content:space-between;align-items:flex-start}
</style>
</head>
<body>

<header>
  <div class="abs brand" style="left:111px;top:14px;font-size:24px">
    <span class="dot" style="width:70px;height:70px"></span><span>Tollbrook<br>Advisory</span>
  </div>
  <div class="abs pin" style="left:748px;top:31px">
    <svg width="34" height="34" viewBox="0 0 24 24"><circle cx="12" cy="12" r="12" fill="var(--ink)"/><path d="M12 5a4.5 4.5 0 0 0-4.5 4.5C7.5 13 12 19 12 19s4.5-6 4.5-9.5A4.5 4.5 0 0 0 12 5zm0 6.3a1.8 1.8 0 1 1 0-3.6 1.8 1.8 0 0 1 0 3.6z" fill="#fff"/></svg>
    <span>214 MERIDIAN WAY, COSTA VERDE, CA 90210</span>
  </div>
  <svg class="abs" style="left:0;top:101px" width="1200" height="57"><rect width="1200" height="57" fill="var(--ink)"/><polygon points="0,0 898,0 870,57 0,57" fill="var(--sage)"/></svg>
  <nav class="nav">
    <a style="left:149px">HOME</a><div class="abs" style="left:149px;top:154px;width:44px;height:2px;background:var(--ink)"></div>
    <span class="sep" style="left:231px">|</span><a style="left:271px">ABOUT</a>
    <span class="sep" style="left:359px">|</span><a style="left:400px">SERVICES</a>
    <span class="sep" style="left:508px">|</span><a style="left:549px">TEAM</a>
    <span class="sep" style="left:626px">|</span><a style="left:666px">CONTACT</a>
    <a style="left:952px;color:#fff">LOGIN</a>
    <span class="sep" style="left:1030px;color:#fff">/</span>
    <a style="left:1068px;color:#fff">SIGN UP</a>
  </nav>
</header>

<section>
  <svg class="abs" style="left:0;top:158px" width="1200" height="670">
    <defs>
      <linearGradient id="heroPhoto" x1="0" x2="1"><stop offset="0" stop-color="#9fb3a9"/><stop offset="0.45" stop-color="#6f7f80"/><stop offset="0.75" stop-color="#26323a"/><stop offset="1" stop-color="#26323a"/></linearGradient>
    </defs>
    <polygon points="0,0 1200,0 1200,476 808,659 0,503" fill="var(--sage)"/>
    <polygon points="0,0 1200,0 1200,462 808,640 0,488" fill="url(#heroPhoto)" role="img" aria-label="Photo of a team of three colleagues working together at a laptop in an office"/>
  </svg>
  <h1 class="abs hero-title">BUILDING SUCCESS IN<br>SOUTHERN <span class="accent">CALIFORNIA</span></h1>
  <p class="abs hero-lead">Expertise at Every Step: From Planning to Execution At Tollbrook, we blend innovative strategies with local market.</p>
  <div class="abs btn btn-light" style="left:642px;top:583px;width:188px;height:62px;font-size:18px">LEARN MORE <svg width="18" height="18" viewBox="0 0 20 20"><circle cx="10" cy="10" r="10" fill="var(--ink)"/><path d="M6 10h7M10 6.5 13.5 10 10 13.5" stroke="#fff" stroke-width="2" fill="none"/></svg></div>
</section>

<section>
  <h2 class="abs" style="left:111px;top:926px;font-size:33px;font-weight:500;color:var(--ink)">Who We <span class="accent">Are</span></h2>
  <p class="abs" style="left:111px;top:990px;width:415px;font-size:15.5px;line-height:34.3px">Welcome to Tollbrook Advisory, your trusted partner in navigating the complexities of the real estate and small business markets. Founded by industry veterans Daniel Reyes and Kevin Park, we specialize in providing comprehensive services tailored to the unique needs of our clients. Whether you're a franchisee, a new restaurant owner, or a commercial real estate investor, our expertise in due diligence, construction management.</p>
  <div class="abs btn btn-dark" style="left:111px;top:1331px;width:186px;height:62px;font-size:18px">OUR MISSION <svg width="18" height="18" viewBox="0 0 20 20"><circle cx="10" cy="10" r="10" fill="#fff"/><path d="M6 10h7M10 6.5 13.5 10 10 13.5" stroke="var(--ink)" stroke-width="2" fill="none"/></svg></div>
  <div class="abs" style="left:588px;top:918px;width:437px;height:421px;border:6px solid #d6e9df"></div>
  <div class="abs" style="left:718px;top:986px;width:371px;height:425px;background:var(--sage)"></div>
  <div class="abs" role="img" aria-label="Photo of a presenter leading a meeting in a glass-walled conference room" style="left:625px;top:947px;width:436px;height:425px;background:linear-gradient(135deg,#b9c6c9,#6d7b80 60%,#3a464d)"></div>
</section>

<section>
  <svg class="abs" style="left:0;top:1470px" width="1200" height="690">
    <polygon points="0,191 392,5 1200,158 1200,690 0,690" fill="var(--mist)"/>
    <polyline points="0,191 392,5 1200,158" fill="none" stroke="var(--sage)" stroke-width="9"/>
  </svg>
  <h2 class="section-title" style="top:1596px">Tollbrook <span class="accent">Services</span></h2>
  <svg class="abs" style="left:26px;top:1887px" width="28" height="20"><path d="M27 10H2M9 3 2 10l7 7" stroke="var(--ink)" stroke-width="2" fill="none"/></svg>
  <svg class="abs" style="left:1143px;top:1887px" width="28" height="20"><path d="M1 10h25M19 3l7 7-7 7" stroke="var(--ink)" stroke-width="2" fill="none"/></svg>

  <div class="card" style="left:93px;width:327px">
    <svg width="80" height="80" viewBox="0 0 80 80" fill="none" stroke="var(--ink)" stroke-width="2.5"><circle cx="40" cy="40" r="22"/><rect x="30" y="32" width="20" height="16" fill="var(--sage)" stroke="none"/><path d="M40 2v12M40 66v12M2 40h12M66 40h12M13 13l9 9M58 58l9 9M67 13l-9 9M22 58l-9 9"/></svg>
    <h3>Franchise Development<br>&amp; Launch</h3>
    <p>At Tollbrook Advisory, our Franchise Development &amp; Launch service is designed to transform</p>
    <div class="btn btn-dark">READ MORE <svg width="14" height="14" viewBox="0 0 20 20"><circle cx="10" cy="10" r="10" fill="#fff"/><path d="M6 10h7M10 6.5 13.5 10 10 13.5" stroke="var(--ink)" stroke-width="2" fill="none"/></svg></div>
  </div>
  <div class="card active" style="left:438px;width:323px">
    <svg width="84" height="84" viewBox="0 0 84 84" fill="none" stroke="#fff" stroke-width="5"><circle cx="50" cy="34" r="24"/><circle cx="50" cy="34" r="10" stroke="var(--sage)" stroke-width="4"/><path d="M32 52 8 76"/></svg>
    <h3>Due Diligence</h3>
    <p>Tollbrook offers comprehensive evaluations tailored to your business needs. We meticulously assess franchise opportunities</p>
    <div class="btn btn-dark" style="top:328px">READ MORE <svg width="14" height="14" viewBox="0 0 20 20"><circle cx="10" cy="10" r="10" fill="#fff"/><path d="M6 10h7M10 6.5 13.5 10 10 13.5" stroke="var(--ink)" stroke-width="2" fill="none"/></svg></div>
  </div>
  <div class="card" style="left:777px;width:325px">
    <svg width="80" height="80" viewBox="0 0 80 80"><path d="M6 38 34 10l28 28h-8v30H14V38z" fill="var(--ink)"/><circle cx="55" cy="55" r="18" fill="var(--sage)" stroke="#fff" stroke-width="3"/><text x="55" y="63" font-size="22" font-weight="700" fill="#fff" text-anchor="middle" font-family="Montserrat,sans-serif">$</text></svg>
    <h3>Investment Property<br>Evaluation</h3>
    <p>Our Investment Property Evaluation Services offer detailed analysis of potential investment</p>
    <div class="btn btn-dark">READ MORE <svg width="14" height="14" viewBox="0 0 20 20"><circle cx="10" cy="10" r="10" fill="#fff"/><path d="M6 10h7M10 6.5 13.5 10 10 13.5" stroke="var(--ink)" stroke-width="2" fill="none"/></svg></div>
  </div>
</section>

<section class="abs" role="img" aria-label="Dimmed photo of business people in discussion behind the call to action" style="left:0;top:2159px;width:1200px;height:449px;background:linear-gradient(90deg,#3b4a52,#2f3d45 50%,#26323a)">
  <h2 style="position:absolute;top:86px;width:1200px;text-align:center;font-size:33px;font-weight:500;color:#fff">Unlock Your Business <span class="accent">Potential Today!</span></h2>
  <p style="position:absolute;left:240px;top:156px;width:720px;text-align:center;font-size:15px;line-height:34px;color:#fff">At Tollbrook Advisory, we're dedicated to turning your business aspirations into reality. Our expertise and commitment ensure you make informed, strategic decisions that drive success. Take the first step towards achieving your goals with confidence.</p>
  <div class="btn btn-light" style="position:absolute;left:506px;top:299px;width:186px;height:62px;font-size:18px">GET STARTED <svg width="18" height="18" viewBox="0 0 20 20"><circle cx="10" cy="10" r="10" fill="var(--ink)"/><path d="M6 10h7M10 6.5 13.5 10 10 13.5" stroke="#fff" stroke-width="2" fill="none"/></svg></div>
</section>

<section>
  <svg class="abs" style="left:0;top:2608px" width="1200" height="720">
    <polygon points="0,0 1200,0 1200,527 808,700 0,560" fill="var(--mist)"/>
    <polyline points="0,560 808,700 1200,527" fill="none" stroke="var(--sage)" stroke-width="9"/>
  </svg>
  <h2 class="section-title" style="top:2695px">Our Leadership <span class="accent">Team</span></h2>
  <div class="member" style="left:111px;background:var(--ink);color:#fff">
    <div class="photo" role="img" aria-label="Portrait photo of principal Daniel Reyes" style="background:linear-gradient(180deg,#9fb4c8,#d8dde0)"></div>
    <div class="info">
      <p>Daniel Reyes brings almost 20 years of rich experience as a real estate investor......</p>
      <h4>DANIEL REYES</h4>
      <div class="role">PRINCIPAL</div>
      <div class="icons">
        <svg width="32" height="32" viewBox="0 0 24 24"><circle cx="12" cy="12" r="12" fill="#fff"/><path d="M8.5 6.5l2 2-1.2 1.5a7 7 0 0 0 4.7 4.7l1.5-1.2 2 2-1.5 1.8A10 10 0 0 1 6.7 8z" fill="var(--ink)"/></svg>
        <svg width="32" height="32" viewBox="0 0 24 24"><circle cx="12" cy="12" r="12" fill="#fff"/><rect x="6.5" y="8" width="11" height="8" fill="var(--ink)"/><path d="M6.5 8 12 12.5 17.5 8" stroke="#fff" fill="none"/></svg>
      </div>
    </div>
  </div>
  <div class="member" style="left:617px;background:#fff;border:2px solid #dfe2e2;color:var(--ink)">
    <div class="photo" role="img" aria-label="Portrait photo of principal Kevin Park" style="background:linear-gradient(180deg,#8a6a55,#2d3338)"></div>
    <div class="info">
      <p>Kevin Park is a seasoned real estate expert with extensive experience in project .....</p>
      <h4>KEVIN PARK</h4>
      <div class="role">PRINCIPAL</div>
      <div class="icons">
        <svg width="32" height="32" viewBox="0 0 24 24"><circle cx="12" cy="12" r="12" fill="var(--ink)"/><path d="M8.5 6.5l2 2-1.2 1.5a7 7 0 0 0 4.7 4.7l1.5-1.2 2 2-1.5 1.8A10 10 0 0 1 6.7 8z" fill="#fff"/></svg>
        <svg width="32" height="32" viewBox="0 0 24 24"><circle cx="12" cy="12" r="12" fill="var(--ink)"/><rect x="6.5" y="8" width="11" height="8" fill="#fff"/><path d="M6.5 8 12 12.5 17.5 8" stroke="var(--ink)" fill="none"/></svg>
      </div>
    </div>
  </div>
</section>

<section>
  <h2 class="section-title" style="top:3398px">Contact <span class="accent">Us</span></h2>
  <div class="field" style="left:180px;top:3492px;width:393px"><span>FULL NAME</span><svg width="16" height="16" viewBox="0 0 16 16"><circle cx="8" cy="5" r="3.5" fill="var(--ink)"/><path d="M2 16a6 6 0 0 1 12 0z" fill="var(--ink)"/></svg></div>
  <div class="field" style="left:625px;top:3492px;width:395px"><span>EMAIL ADDRESS</span><svg width="18" height="14" viewBox="0 0 18 14"><rect width="18" height="14" fill="var(--ink)"/><path d="M0 0 9 8 18 0" stroke="#fff" fill="none"/></svg></div>
  <div class="field" style="left:180px;top:3567px;width:393px"><span>PHONE NUMBER</span><svg width="16" height="16" viewBox="0 0 24 24"><path d="M5 2l4 4-2 3a12 12 0 0 0 8 8l3-2 4 4-3 3A19 19 0 0 1 2 5z" fill="var(--ink)"/></svg></div>
  <div class="field" style="left:625px;top:3567px;width:395px"><span>COMPANY</span><svg width="18" height="18" viewBox="0 0 18 18"><rect x="1" y="2" width="9" height="16" fill="var(--ink)"/><rect x="11" y="8" width="6" height="10" fill="var(--ink)"/></svg></div>
  <div class="field" style="left:180px;top:3644px;width:840px;height:66px"><span>TYPE YOUR MESSAGE</span><svg width="17" height="16" viewBox="0 0 17 16"><ellipse cx="8.5" cy="7" rx="8" ry="6.5" fill="var(--ink)"/><path d="M3 12 2 16l5-3z" fill="var(--ink)"/></svg></div>
  <div class="abs btn btn-dark" style="left:503px;top:3766px;width:194px;height:60px;font-size:18px">GET IN TOUCH <svg width="18" height="18" viewBox="0 0 20 20"><circle cx="10" cy="10" r="10" fill="#fff"/><path d="M6 10h7M10 6.5 13.5 10 10 13.5" stroke="var(--ink)" stroke-width="2" fill="none"/></svg></div>
</section>

<footer class="abs" style="left:0;top:3922px;width:1200px;height:284px;background:var(--ink-deep)">
  <div class="abs brand" style="left:111px;top:56px;font-size:34px;color:#fff">
    <span class="dot" style="width:110px;height:110px;border-width:7px"></span><span style="line-height:40px">Tollbrook<br>Advisory</span>
  </div>
  <div class="abs pin" style="left:508px;top:100px;color:#fff">
    <svg width="34" height="34" viewBox="0 0 24 24"><circle cx="12" cy="12" r="12" fill="#fff"/><path d="M8.5 6.5l2 2-1.2 1.5a7 7 0 0 0 4.7 4.7l1.5-1.2 2 2-1.5 1.8A10 10 0 0 1 6.7 8z" fill="var(--ink)"/></svg>
    <span>+1 555 010 0199</span>
  </div>
  <div class="abs pin" style="left:748px;top:100px;color:#fff">
    <svg width="34" height="34" viewBox="0 0 24 24"><circle cx="12" cy="12" r="12" fill="#fff"/><path d="M12 5a4.5 4.5 0 0 0-4.5 4.5C7.5 13 12 19 12 19s4.5-6 4.5-9.5A4.5 4.5 0 0 0 12 5zm0 6.3a1.8 1.8 0 1 1 0-3.6 1.8 1.8 0 0 1 0 3.6z" fill="var(--ink)"/></svg>
    <span>214 MERIDIAN WAY, COSTA VERDE, CA 90210</span>
  </div>
  <p class="abs" style="left:0;top:207px;width:1200px;text-align:center;font-size:17px;font-weight:600;color:#fff">PRIVACY POLICY &nbsp;|&nbsp; DISCLAIMER &nbsp;|&nbsp; TOLLBROOK ADVISORY &nbsp;© 2024</p>
</footer>

</body>
</html>
```